New Innovative Counselling and psychotherapy Service needs Business Card design

Keep it simple and professional. On one side, just company name and logo (perhaps in all blue) and maybe a tag line.

On other side (all white) my name and Qualifications in centre

Industry/Entity Type

Health And Wellness

Contact Information for Business Card

Dara Whelby
Counsellor & Psychotherapist
BSc (Psychol.), BA, Dip. (Couns. & Psych.), PG.Cert (CBT), FGTrK, ONRE

I will also require Mobile no, Email and web site address of which I'll pass on to final designer.

Font styles to use
Sans Serif

Requirements
Must have
• My Logo Only and please use the colours in logo that is in it.
Should not have
• Any other images

```html
<!DOCTYPE html>
<html lang="en">
<head>
<meta charset="utf-8">
<title>Bright Meadow – Business Card</title>
<link href="https://fonts.googleapis.com/css2?family=Questrial&family=Roboto:wght@400;500;700&display=swap" rel="stylesheet">
<style>
  :root {
    --bg: #e9eaec;
    --card-white: #ffffff;
    --blue: #3aa5e4;
    --blue-soft: #6cc0ea;
    --teal: #7cc9b8;
    --green: #8cc850;
    --green-soft: #a6d87a;
    --ink: #333638;
    --ink-soft: #55595c;
  }
  * { box-sizing: border-box; margin: 0; padding: 0; }
  html, body { width: 1200px; height: 726px; overflow: hidden; }
  body {
    background: var(--bg);
    font-family: "Roboto", Arial, sans-serif;
    position: relative;
  }
  .card {
    position: absolute;
    top: 208px;
    width: 540px;
    height: 310px;
    overflow: hidden;
    box-shadow: 0 6px 18px rgba(0,0,0,0.12);
  }
  /* Front side */
  .card-front {
    left: 40px;
    background: linear-gradient(110deg, var(--blue-soft) 0%, var(--teal) 50%, var(--green-soft) 85%, var(--green) 100%);
  }
  .card-front .front-glow {
    position: absolute; inset: 0;
  }
  .card-front .brand-name {
    position: absolute;
    left: 0; right: 0; top: 128px;
    text-align: center;
    font-family: "Questrial", Arial, sans-serif;
    font-size: 50px;
    color: #fff;
    letter-spacing: 0.5px;
  }
  /* Back side */
  .card-back {
    left: 620px;
    background: var(--card-white);
  }
  .brand-lockup {
    position: absolute;
    left: 40px; top: 88px;
    display: flex; align-items: center; gap: 18px;
  }
  .brand-dot {
    width: 58px; height: 58px; border-radius: 50%;
    background: var(--blue);
  }
  .brand-lockup .brand-name {
    font-family: "Questrial", Arial, sans-serif;
    font-size: 40px;
    color: var(--ink);
  }
  .contact-list {
    position: absolute;
    left: 312px; top: 168px;
    list-style: none;
    font-size: 13px;
    color: var(--ink);
  }
  .contact-list li {
    display: flex; align-items: center; gap: 8px;
    height: 19px;
  }
  .contact-list svg { width: 12px; height: 12px; flex: none; }
  .person {
    position: absolute;
    left: 30px; top: 210px;
  }
  .person-name {
    font-size: 23px; font-weight: 700;
    color: var(--blue);
    margin-bottom: 3px;
  }
  .person-role, .person-quals {
    font-size: 12.5px;
    color: var(--ink-soft);
    line-height: 1.3;
  }
  .footer-bands {
    position: absolute; left: 0; bottom: 0;
    width: 540px; height: 50px;
  }
  .tagline {
    position: absolute;
    right: 28px; bottom: 14px;
    font-size: 13px;
    color: #fff;
  }
</style>
</head>
<body>

  <section class="card card-front" aria-label="Card front">
    <div class="front-glow" role="img" aria-label="Soft blue to green background wash"></div>
    <div class="brand-name">Bright Meadow</div>
  </section>

  <section class="card card-back" aria-label="Card back">
    <div class="brand-lockup">
      <div class="brand-dot"></div>
      <div class="brand-name">Bright Meadow</div>
    </div>

    <ul class="contact-list">
      <li>
        <svg viewBox="0 0 12 12"><path fill="#3a9a8a" d="M2.5 1l2 2-1 1.2c.6 1.4 1.7 2.5 3.1 3.1L7.8 6.3l2 2-1.3 1.6C5 9.5 2.3 6.8 1 3.3z"/></svg>
        0987 654 3210
      </li>
      <li>
        <svg viewBox="0 0 12 12"><rect x="1" y="2.5" width="10" height="7" fill="none" stroke="#3a9a8a" stroke-width="1.2"/><path d="M1 2.5l5 4 5-4" fill="none" stroke="#3a9a8a" stroke-width="1.2"/></svg>
        dara.w@BrightMeadow.com
      </li>
      <li>
        <svg viewBox="0 0 12 12"><circle cx="6" cy="6" r="4.8" fill="none" stroke="#3a9a8a" stroke-width="1.2"/><path d="M1.2 6h9.6M6 1.2c-2 2.6-2 7 0 9.6M6 1.2c2 2.6 2 7 0 9.6" fill="none" stroke="#3a9a8a" stroke-width="0.9"/></svg>
        www.BrightMeadow.com
      </li>
    </ul>

    <div class="person">
      <div class="person-name">Dara Whelby</div>
      <div class="person-role">Counsellor &amp; Psychotherapist</div>
      <div class="person-quals">BSc (Psychol.), BA, Dip. (Couns. &amp;<br>Psych.), PG.Cert (CBT), FGTrK, ONRE</div>
    </div>

    <svg class="footer-bands" viewBox="0 0 540 50" preserveAspectRatio="none" aria-hidden="true">
      <rect x="0" y="41" width="540" height="9" fill="var(--green)"/>
      <path d="M318 50 L330 8 Q332 2 338 2 L540 2 L540 50 Z" fill="var(--blue)"/>
    </svg>
    <div class="tagline">A tag line goes here</div>
  </section>

</body>
</html>
```